Executive Business Card for Healthcare Company [Need Today]

I need a business card design for a healthcare company. The only branding the company has thus far is a logo. The cards will be utilized by company executives. The design I envision will be vibrant and appealing but with a corporate feel. They shouldn't be too casual or playful. I would like to complete this project TODAY if possible.

Target Market(s)

Healthcare vendors, other executives in healthcare and pharmaceuticals

Industry/Entity Type

Pharmaceutical

Contact Information for Business Card

See attachment

Font styles to use
Serif
Sans Serif

Colors

Designer to choose colors to be used in the design.

```html
<!DOCTYPE html>
<html lang="en">
<head>
<meta charset="utf-8">
<title>Meridale Therapeutics – Business Card</title>
<link href="https://fonts.googleapis.com/css2?family=Jost:wght@400;500;600&display=swap" rel="stylesheet">
<style>
  :root {
    --teal: #36bfc5;
    --green: #66c197;
    --white: #ffffff;
    --backdrop: #e9ecec;
  }
  * { margin: 0; padding: 0; box-sizing: border-box; }
  html, body {
    width: 1200px; height: 1189px; overflow: hidden;
    background: var(--backdrop);
    font-family: "Jost", sans-serif;
  }
  .card {
    position: absolute; left: 160px;
    width: 880px; height: 503px;
    border-radius: 26px; overflow: hidden;
    box-shadow: 0 6px 20px rgba(0,0,0,.12);
  }
  .card-front { top: 60px; background: var(--white); }
  .card-back { top: 626px; background: var(--teal); }

  /* front */
  .front-brand {
    position: absolute; left: 50%; top: 50%;
    transform: translate(-50%, -50%);
    display: flex; align-items: center; gap: 22px;
  }
  .brand-ring {
    flex: none;
    width: 112px; height: 112px; border-radius: 50%;
    border: 4px solid var(--green);
  }
  .brand-name {
    color: var(--teal); font-weight: 500; font-size: 40px;
    letter-spacing: .5px; line-height: 1; white-space: nowrap;
  }

  /* back */
  .back-disc {
    position: absolute; left: 470px; top: -70px;
    width: 620px; height: 620px; border-radius: 50%;
    background: var(--white);
  }
  .back-ring {
    position: absolute; left: 520px; top: -20px;
    width: 520px; height: 520px; border-radius: 50%;
    border: 10px solid var(--green);
    display: flex; align-items: center; justify-content: flex-start;
    padding-left: 62px;
  }
  .back-ring .brand-name { font-size: 38px; line-height: 1.1; text-align: center; }
  .side-notch {
    position: absolute; left: -18px; top: 108px;
    width: 36px; height: 36px; border-radius: 50%;
    background: var(--backdrop);
  }
  .holder { position: absolute; left: 60px; top: 92px; color: var(--white); }
  .holder-name { font-size: 28px; font-weight: 600; line-height: 1.1; }
  .holder-title { font-size: 19px; font-weight: 400; }
  .contact-list {
    position: absolute; left: 62px; top: 262px;
    list-style: none; color: var(--white); font-size: 22px; line-height: 31px;
  }
  .contact-list li { display: flex; align-items: center; gap: 10px; }
  .contact-list svg { width: 20px; height: 20px; flex: none; }
  .company-address {
    position: absolute; left: 62px; top: 372px;
    color: var(--white); font-style: normal; font-size: 22px; line-height: 29px;
  }
  .company-address strong { font-weight: 600; }
</style>
</head>
<body>

<section class="card card-front" aria-label="Card front">
  <div class="front-brand">
    <div class="brand-ring"></div>
    <span class="brand-name">Meridale Therapeutics</span>
  </div>
</section>

<section class="card card-back" aria-label="Card back">
  <div class="side-notch"></div>
  <div class="back-disc"></div>
  <div class="back-ring"><span class="brand-name">Meridale<br>Therapeutics</span></div>

  <div class="holder">
    <p class="holder-name">Daniel Whitcomb</p>
    <p class="holder-title">Senior Director of Marketing</p>
  </div>

  <ul class="contact-list">
    <li>
      <svg viewBox="0 0 20 20" fill="none" stroke="#fff" stroke-width="1.5"><circle cx="10" cy="10" r="9"/><rect x="7" y="5" width="6" height="10" rx="1"/></svg>
      555-214-0387
    </li>
    <li>
      <svg viewBox="0 0 20 20" fill="none" stroke="#fff" stroke-width="1.5"><circle cx="10" cy="10" r="9"/><path d="M5.5 9c0-2 9-2 9 0M7 10h6l1 4H6z"/></svg>
      555-610-2294
    </li>
    <li>
      <svg viewBox="0 0 20 20" fill="none" stroke="#fff" stroke-width="1.5"><circle cx="10" cy="10" r="9"/><rect x="5" y="6.5" width="10" height="7"/><path d="M5 6.5l5 4 5-4"/></svg>
      dwhitcomb@meridalerx.com
    </li>
  </ul>

  <address class="company-address">
    <strong>Meridale Therapeutics, LLC</strong><br>
    118 N Lumpkin Avenue<br>
    Dalton, GA 30720
  </address>
</section>

</body>
</html>
```